Marlowby Services Website Design

We have most content but require a professional design. We have a logo already and will need it utilized along with several of the photos from the attached documentation.
First page should have our mission and Vision and the synapsis provided in the word document. Visitors will be prompted to select from one of our 3 divisions from this page.
Each division will have the same list of tabs : About, Services, Safety, Careers and Contact.
Photos on each divisions page should be representative of the divisions offerings. The word doc attached contains the requested content and we are open to edits that would complement and fill the website.
I like the Quorvane site www.quorvane.example - they are our competition so cant be modeled directly after this.
Please include prompts to request quote at each service page. align the format of the geotechnical page to the other 2 divisions.
I used chat gpt for some of the content so will need it optimized for SCO.

```html
<!DOCTYPE html>
<html lang="en">
<head>
<meta charset="UTF-8">
<title>Marlowby Services</title>
<link rel="stylesheet" href="https://fonts.googleapis.com/css2?family=Orbitron:wght@700;900&family=Poppins:wght@400;500;600&family=Oswald:wght@600&family=Lato:wght@400&display=swap">
<style>
:root{
  --red:#ec1c24;
  --black:#0d0b0b;
  --ink:#1d1d1d;
  --grey:#4a4a4a;
  --white:#ffffff;
  --line:#3a3a3a;
}
*{margin:0;padding:0;box-sizing:border-box}
html,body{width:1200px;height:2801px;overflow:hidden;background:var(--white)}
.page{position:relative;width:1200px;height:2801px;font-family:"Poppins",sans-serif;color:var(--ink)}
.abs{position:absolute}
.brand{font-family:"Orbitron",sans-serif;font-weight:900;color:var(--red);letter-spacing:2px}
.display{font-family:"Orbitron",sans-serif;font-weight:900;letter-spacing:4px}

.header-brand{left:141px;top:14px;font-size:36px}
.header-phone{right:140px;top:22px;display:flex;align-items:center;gap:10px;font-weight:600;font-size:22px;letter-spacing:2px;color:var(--ink)}

.hero{left:0;top:76px}
.hero-title{left:141px;top:254px;color:var(--white);font-size:48px;line-height:61px}
.select-label{left:0;width:1200px;top:615px;text-align:center;color:var(--white);font-size:15px;letter-spacing:2px;font-weight:500}
.division{width:240px;text-align:center;font-size:16px;font-weight:500;line-height:23px;color:var(--ink)}
.division-icon{position:absolute;width:84px;height:84px;border-radius:50%;background:var(--red);border:5px solid var(--white);box-shadow:0 2px 6px rgba(0,0,0,.18);display:flex;align-items:center;justify-content:center}

.section-title{left:0;width:1200px;top:846px;text-align:center;font-size:33px}
.section-title .accent{color:var(--red)}
.service-photo{top:921px;width:437px;height:316px;border-radius:12px}
.photo-truck{left:141px;background:linear-gradient(180deg,#8fb3d9 0%,#9aa78f 30%,#eaeaea 45%,#5b574e 75%,#4f4a40 100%)}
.photo-worker{left:621px;background:linear-gradient(160deg,#c6d3e4 0%,#a9b6c6 40%,#6b4a36 70%,#3f4e3e 100%)}
.service-caption{top:1265px;width:437px;text-align:center;font-size:17.5px;line-height:26px}

.vision-band{left:0;top:1442px;width:700px;height:314px;background:var(--red);clip-path:polygon(0 0,674px 0,554px 314px,0 314px)}
.vision-photo{left:548px;top:1400px;width:652px;height:404px;clip-path:polygon(160px 0,652px 0,652px 404px,14px 404px,0 388px,137px 30px);background:linear-gradient(170deg,#b8c4cf 0%,#7d8a83 35%,#6e7066 60%,#4e5549 100%)}
.vision-title{left:141px;top:1520px;color:var(--white);font-size:33px}
.vision-text{left:141px;top:1570px;width:410px;color:var(--white);font-size:15px;line-height:25.5px}

.dots{left:104px;top:1875px;width:110px;height:110px;background:#eeeeee}
.mission-photo{left:141px;top:1891px;width:381px;height:378px;border-radius:10px;background:linear-gradient(180deg,#3b77c7 0%,#7fa8df 45%,#d9d9d9 62%,#8a8780 85%,#6c6a62 100%)}
.badge{left:428px;top:2174px;width:143px;height:143px;background:var(--white);border-radius:14px}
.badge-inner{left:435px;top:2181px;width:129px;height:129px;background:var(--red);border-radius:10px;color:var(--white);text-align:center}
.badge-num{font-family:"Oswald",sans-serif;font-weight:600;font-size:62px;line-height:62px;margin-top:14px}
.badge-label{font-size:13px;line-height:16px;letter-spacing:1px;margin-top:10px}
.mission-title{left:617px;top:1950px;font-size:33px}
.mission-title .accent{color:var(--red)}
.mission-text{left:617px;top:2005px;width:445px;font-size:15px;line-height:25.5px;color:var(--grey)}
.mission-text p+p{margin-top:11px}
.mission-text strong{color:var(--ink);font-weight:600}

.footer{left:0;top:2388px;width:1200px;height:413px;background:var(--black);color:var(--white)}
.footer-brand{left:0;width:1200px;top:80px;text-align:center;font-size:36px}
.footer-rule{left:141px;width:921px;height:1px;background:var(--line)}
.footer-nav{left:141px;width:921px;top:197px;font-family:"Lato",sans-serif;font-size:13px}
.footer-nav a{position:absolute;color:var(--white);text-decoration:none;transform:translateX(-50%);white-space:nowrap}
.contact{display:flex;align-items:center;gap:10px;font-family:"Lato",sans-serif;font-size:13px;line-height:20px}
.contact-icon{width:30px;height:30px;border-radius:50%;border:1px solid var(--red);display:flex;align-items:center;justify-content:center;flex:none}
.contact-head{font-family:"Poppins",sans-serif;font-size:14px;font-weight:500}
.copyright{left:0;width:1200px;top:377px;text-align:center;font-family:"Lato",sans-serif;font-size:12px}
</style>
</head>
<body>
<div class="page">

  <header>
    <div class="abs brand header-brand">MARLOWBY</div>
    <div class="abs header-phone">
      <svg width="26" height="26" viewBox="0 0 24 24" fill="none" stroke="#ec1c24" stroke-width="2" stroke-linecap="round" stroke-linejoin="round"><path d="M22 16.9v3a2 2 0 0 1-2.2 2 19.8 19.8 0 0 1-8.6-3.1 19.5 19.5 0 0 1-6-6A19.8 19.8 0 0 1 2.1 4.2 2 2 0 0 1 4.1 2h3a2 2 0 0 1 2 1.7c.1 1 .4 1.9.7 2.8a2 2 0 0 1-.5 2.1L8 9.9a16 16 0 0 0 6 6l1.3-1.3a2 2 0 0 1 2.1-.4c.9.3 1.8.6 2.8.7a2 2 0 0 1 1.7 2z"/><path d="M15 2a7 7 0 0 1 7 7M15 6a3 3 0 0 1 3 3"/></svg>
      587.555.0142
    </div>
  </header>

  <section class="hero-section">
    <svg class="abs hero" width="1200" height="640" viewBox="0 76 1200 640" role="img" aria-label="Aerial photo of a boom truck lifting a work platform beside a road and houses">
      <defs>
        <linearGradient id="heroFill" x1="0" y1="0" x2="1" y2="1">
          <stop offset="0" stop-color="#9a9a94"/>
          <stop offset="0.45" stop-color="#8a8369"/>
          <stop offset="0.7" stop-color="#7d7b6e"/>
          <stop offset="1" stop-color="#8c8f8d"/>
        </linearGradient>
      </defs>
      <path d="M0 76 H1200 V609 Q600 783 0 609 Z" fill="url(#heroFill)"/>
    </svg>
    <h1 class="abs display hero-title">SAFETY.<br>QUALITY.<br>SERVICE.</h1>
    <div class="abs select-label">SELECT DIVISION:</div>

    <div class="abs division-icon" style="left:290px;top:637px">
      <svg width="40" height="40" viewBox="0 0 40 40" fill="none" stroke="#fff" stroke-width="2" stroke-linejoin="round"><rect x="6" y="28" width="22" height="5"/><circle cx="10" cy="35" r="2"/><circle cx="24" cy="35" r="2"/><path d="M12 28 L26 12"/><rect x="24" y="6" width="10" height="6"/><rect x="8" y="20" width="8" height="8"/></svg>
    </div>
    <div class="abs division-icon" style="left:557px;top:654px">
      <svg width="40" height="40" viewBox="0 0 40 40" fill="none" stroke="#fff" stroke-width="2" stroke-linejoin="round"><rect x="5" y="26" width="20" height="7"/><circle cx="9" cy="35" r="2"/><circle cx="21" cy="35" r="2"/><path d="M27 4 V30 M31 4 V30 M27 10 H31 M27 18 H31"/><path d="M29 30 V37"/><rect x="10" y="18" width="10" height="8"/></svg>
    </div>
    <div class="abs division-icon" style="left:825px;top:637px">
      <svg width="40" height="40" viewBox="0 0 40 40" fill="none" stroke="#fff" stroke-width="2" stroke-linecap="round" stroke-linejoin="round"><path d="M14 27 C10 24 9 20 9 17 a11 11 0 0 1 22 0 c0 3-1 7-5 10 v3 H14 z"/><path d="M15 34 H25 M17 37 H23"/><path d="M20 2 V5 M5 17 H2 M38 17 H35 M8 6 L10 8 M32 6 L30 8"/></svg>
    </div>

    <div class="abs division" style="left:212px;top:726px">Aerial Access</div>
    <div class="abs division" style="left:479px;top:743px">Geotechnical Drilling</div>
    <div class="abs division" style="left:748px;top:726px">Renewable Energy<br>Services</div>
  </section>

  <section class="service-section">
    <h2 class="abs display section-title"><span class="accent">MARLOWBY</span> SERVICE</h2>
    <div class="abs service-photo photo-truck" role="img" aria-label="Photo of a white boom truck parked on a gravel yard"></div>
    <div class="abs service-photo photo-worker" role="img" aria-label="Photo of a worker in safety vest servicing a wellhead beside a steel tower"></div>
    <p class="abs service-caption" style="left:141px">Delivering Safe, Reliable <strong>Aerial Access</strong></p>
    <p class="abs service-caption" style="left:621px"><strong>Maintenance services</strong> to Oil&amp;Gas, Construction, Utility, &amp; Renewable energy industries.</p>
  </section>

  <section class="vision-section">
    <div class="abs vision-band"></div>
    <div class="abs vision-photo" role="img" aria-label="Aerial photo of a boom truck raising a company sign over a small town"></div>
    <h2 class="abs display vision-title">OUR VISION:</h2>
    <p class="abs vision-text">To be the leading provider of aerial access, geotechnical drilling, and service solutions, setting the standard for excellence in safety, efficiency, and environmental stewardship.</p>
  </section>

  <section class="mission-section">
    <div class="abs dots" role="img" aria-label="Decorative dot pattern"></div>
    <div class="abs mission-photo" role="img" aria-label="Photo of a boom truck parked in front of a town water tower"></div>
    <div class="abs badge"></div>
    <div class="abs badge-inner">
      <div class="badge-num">65+</div>
      <div class="badge-label">YEARS OF<br>EXPERIENCE</div>
    </div>
    <h2 class="abs display mission-title"><span class="accent">OUR</span> MISSION</h2>
    <div class="abs mission-text">
      <p><strong>At Marlowby, our mission</strong> is to deliver unparalleled aerial access, geotechnical drilling, and service and maintenance solutions, consistently exceeding our clients’ expectations.</p>
      <p>We strive to achieve this by investing in cutting-edge technology, fostering a culture of safety and continuous improvement, and prioritizing environmental sustainability. Through collaboration, integrity, and dedication, we aim to contribute to the success of our clients while maintaining the highest standards of quality and professionalism.</p>
    </div>
  </section>

  <footer class="abs footer">
    <div class="abs brand footer-brand">MARLOWBY</div>
    <div class="abs footer-rule" style="top:159px"></div>
    <nav class="abs footer-nav">
      <a href="#" style="left:198px">Home</a>
      <a href="#" style="left:290px">About</a>
      <a href="#" style="left:389px">Services</a>
      <a href="#" style="left:489px">Safety</a>
      <a href="#" style="left:586px">Careers</a>
      <a href="#" style="left:700px;font-size:14px">Contact Us</a>
    </nav>
    <div class="abs footer-rule" style="top:250px"></div>

    <div class="abs contact" style="left:198px;top:285px">
      <span class="contact-icon"><svg width="14" height="14" viewBox="0 0 24 24" fill="#ec1c24"><path d="M12 2a7 7 0 0 0-7 7c0 5 7 13 7 13s7-8 7-13a7 7 0 0 0-7-7zm0 9.5A2.5 2.5 0 1 1 12 6.5a2.5 2.5 0 0 1 0 5z"/></svg></span>
      <span>118 Ridgeline Road Fernmoor<br>Alberta&nbsp; T0K 4B7</span>
    </div>
    <div class="abs contact" style="left:525px;top:285px">
      <span class="contact-icon"><svg width="13" height="13" viewBox="0 0 24 24" fill="#ec1c24"><path d="M22 16.9v3a2 2 0 0 1-2.2 2 19.8 19.8 0 0 1-8.6-3.1 19.5 19.5 0 0 1-6-6A19.8 19.8 0 0 1 2.1 4.2 2 2 0 0 1 4.1 2h3a2 2 0 0 1 2 1.7c.1 1 .4 1.9.7 2.8a2 2 0 0 1-.5 2.1L8 9.9a16 16 0 0 0 6 6l1.3-1.3a2 2 0 0 1 2.1-.4c.9.3 1.8.6 2.8.7a2 2 0 0 1 1.7 2z"/></svg></span>
      <span><span class="contact-head">Phone</span><br>(587)-555-0199</span>
    </div>
    <div class="abs contact" style="left:792px;top:287px">
      <span class="contact-icon"><svg width="13" height="13" viewBox="0 0 24 24" fill="#ec1c24"><path d="M2 5h20v14H2z" fill="none" stroke="#ec1c24" stroke-width="2"/><path d="M2 6l10 7 10-7" fill="none" stroke="#ec1c24" stroke-width="2"/></svg></span>
      <span><span class="contact-head">Email</span><br>career@marlowbyservices.example</span>
    </div>

    <div class="abs footer-rule" style="top:355px"></div>
    <div class="abs copyright">© 2024 <strong>MARLOWBY</strong>. All Rights Reserved.</div>
  </footer>

</div>
</body>
</html>
```